Stock Broking Firm - Web Design Project

We are looking at doing a full re-design of our home page and content page and moving the majority of our content over to DNN.

Phase 1 : Website redesign www.kvtrading.com.au

The current design is too washed out, boring and has no call to action buttons.

Solution:

KV Trading is looking for a brighter/ cleaner redesign with a few stand out call to action buttons.

• Banner with logo across the top horizontally - Bright blue logo on white background similar to www.dlq.com.au - CALL 1300 482 917 - Follow on Chirpline / Friendwall
• Horizontal menu bar - professional looking. - Home - About Us- Our Services - Membership - Open an Account - Become a member - Contact
• Below banner top left - large rotating banner - maybe zumbo gallery style www.tgwhitfields.com.au
• Right of rotating banner - Membership login
• Below members login - Register for Daily Market Report/ research blog - Large bright button / Name / Email / Phone / pop up??
• Below Register for daily market report - Market Indicies - RSS feed of delayed data from Vantro see www.tgwhitfields.com
• Below Market indicies - KV TRADING - Market Tweets ( feed from our chirpline page)

Below Rotating Banner -

content area

Below content area - 4 large block buttons see www.harkvine.com.au ( hover over change colour)

Button 1 - EDUCATION - content - click here for more

Button 2 - Market Information and Research

Button 3 - Full service Broker - content brief - click here for more

Button 4 - Trade Commodities and Options

below buttons - small horizontal menu bar slightly different colour incl - Careers/ Partners / Legal Privacy FSG Site Map

Regards,
Owen Pettit

Target Market(s)

35 - 65

Industry/Entity Type

Education

Requirements
Must have
• Follow brief above - large banner, call to action buttons, F.W. Chirpline, Member login etc. 4 big buttons
Nice to have
• clean looking site similar to www.dlq.com.au / not too busy. Corporate looking.
Should not have
• not too busy

```html
<!DOCTYPE html>
<html lang="en">
<head>
<meta charset="utf-8">
<title>KV Trading</title>
<link rel="stylesheet" href="https://fonts.googleapis.com/css2?family=Open+Sans:wght@400;600;700&display=swap">
<style>
:root{
  --blue:#1596d8;
  --blue-dark:#0b7fc0;
  --blue-text:#1685c8;
  --text:#555b60;
  --dark:#3c4247;
  --border:#dcdfe2;
  --row:#e7f3fb;
  --red:#d0262b;
  --green:#3a9a1c;
  --panel:#f3f4f5;
}
*{box-sizing:border-box;margin:0;padding:0}
html,body{width:845px;height:1200px;overflow:hidden}
body{font-family:"Open Sans",Arial,sans-serif;color:var(--text);background:linear-gradient(#ededed 0,#fff 14px,#fff 100%);position:relative;font-size:8.2px;line-height:11.4px}
a{color:var(--blue-text);text-decoration:none}
.abs{position:absolute}

/* header */
.brand{left:112px;top:14px;width:250px}
.brand-mark{display:flex;align-items:center;gap:8px}
.brand-mark .sq{width:24px;height:24px;background:var(--blue-dark)}
.brand-name{font-size:33px;font-weight:600;color:#0f5e8c;line-height:40px;letter-spacing:-.3px}
.brand-tag{font-size:7.2px;line-height:9.5px;color:var(--dark);text-align:right;margin-right:10px}
.call{right:113px;top:12px;font-size:11px;color:var(--dark)}
.call b{color:var(--blue-text);font-weight:700}
.follow{right:113px;top:60px;display:flex;align-items:center;gap:6px;font-size:11px;color:var(--dark)}
.social{font-size:8px;font-weight:600;color:#fff;background:var(--blue-dark);padding:4px 4px;line-height:10px}

/* nav */
.nav{left:112px;top:88px;width:620px;height:25px;background:linear-gradient(#23a9ea,#0f8cd2);border-radius:2px;display:flex;justify-content:space-around;align-items:center}
.nav a{color:#fff;font-size:10.5px;font-weight:600}

/* banner */
.banner{left:112px;top:128px;width:433px;height:184px;background:linear-gradient(100deg,#b9c9d9 0%,#dfe7ef 45%,#c8d3de 100%);overflow:hidden}
.banner-caption{position:absolute;left:0;bottom:0;width:100%;height:43px;background:rgba(17,138,204,.93);color:#fff;padding:9px 10px}
.banner-caption strong{display:block;font-size:10.5px;line-height:13px}
.banner-caption span{font-size:8.2px}
.thumbs{position:absolute;right:11px;top:11px;display:flex;gap:3px}
.thumbs i{display:block;width:52px;height:22px;background:linear-gradient(#6d8fb3,#375f86)}

/* sidebar */
.panel{border:1px solid var(--border);background:#fff;left:558px;width:174px}
.panel-title{color:var(--blue-text);font-size:10.5px;font-weight:700;padding:10px 13px 0;line-height:13px}
.login{top:128px;height:184px;background:var(--panel)}
.login .panel-title{background:linear-gradient(#24a8e8,#108bd1);color:#fff;height:32px;padding-top:9px}
.login label{display:block;font-size:8.6px;color:var(--dark);margin:10px 12px 3px}
.login .field{margin:0 12px;height:22px;background:#fff;border:1px solid #d5d8db;border-radius:3px}
.login .links{margin:10px 12px 0;font-size:8px}
.btn-login{display:inline-block;margin:6px 12px;background:var(--blue);color:#fff;font-weight:700;font-size:10px;padding:4px 10px;border-radius:3px}
.cta{left:558px;top:326px;width:174px;height:51px;background:linear-gradient(#25aaea,#0f8bd0);color:#fff;font-size:12.5px;font-weight:700;text-align:center;line-height:16px;padding-top:9px;border-radius:2px}
.indices{top:390px;height:180px}
table{border-collapse:collapse;width:172px;margin-top:14px;font-size:7.8px}
th{color:var(--blue-text);font-weight:600;height:15px}
td{height:16.5px;padding:0 2px}
tr:nth-child(even) td{background:var(--row)}
td:first-child{padding-left:9px}
.dn{color:var(--red)}.up{color:var(--green)}
.news{top:578px;height:274px}
.news ul{list-style:none;margin:8px 10px 0}
.news li{display:flex;gap:6px;border-bottom:1px solid #e8eaec;padding:3px 0 4px;line-height:11px}
.news li time{font-size:7.5px;white-space:nowrap;color:var(--dark)}
.news-foot{display:flex;justify-content:space-between;align-items:center;margin:4px 10px}
.news-foot b{color:#1b3d6e;font-size:10px}
.more{background:#eceeef;border-radius:3px;padding:1px 6px;font-size:8px;color:var(--dark)}
.tweets{top:866px;height:246px}
.tweets .tw{margin:0 12px;border-bottom:1px solid #e8eaec;padding:7px 0}
.tweets .tw:first-of-type{margin-top:6px}
.tweets small{display:block;color:#999;font-size:7.5px;margin-top:3px}
.tweets .follow-tw{margin:6px 12px;font-weight:600;font-size:8.4px}

/* content */
.content{left:112px;top:330px;width:433px;line-height:12.2px}
.content h1{font-size:11px;font-weight:600;color:var(--blue-text);line-height:13px;padding-bottom:10px;border-bottom:1px solid var(--border);margin-bottom:13px}
.content p{margin-bottom:13px}
.adv{list-style:none;margin:0 8px 13px 10px}
.adv li{display:flex;gap:10px;margin-bottom:10px}
.adv .num{flex:none;width:15px;height:15px;border-radius:50%;background:#e6e7e8;text-align:center;line-height:15px;color:var(--dark)}
.services a{margin:0 5px}

/* boxes */
.box{width:209px;height:110px;border:1px solid var(--border);background:linear-gradient(#fff,#efefef);padding:9px 12px;border-radius:2px}
.box h2{font-size:10.5px;font-weight:700;color:var(--blue-text);line-height:12px;margin-bottom:6px;min-height:24px}
.box p{color:var(--dark);font-size:8.2px;line-height:11.6px;margin-bottom:4px}
.box.active{background:var(--blue);border-color:var(--blue)}
.box.active h2,.box.active p,.box.active a{color:#fff}

/* footer */
.footer{left:112px;top:1133px;width:620px;border-top:1px solid var(--border);padding-top:10px;font-size:8.2px}
.footer .right{position:absolute;right:0;top:20px;display:flex;gap:12px;align-items:center;color:var(--dark)}
</style>
</head>
<body>

<header>
  <div class="abs brand">
    <div class="brand-mark"><span class="sq"></span><span class="brand-name">KV Trading</span></div>
    <div class="brand-tag">shares | options | commodities | foreign exchange<br>ABN 47 203 615 882 | licence no 402 719</div>
  </div>
  <div class="abs call">CALL <b>1300 482 917</b></div>
  <div class="abs follow">Follow on <span class="social">Friendwall</span><span class="social">Chirpline</span></div>
  <nav class="abs nav">
    <a href="#">Home</a><a href="#">About Us</a><a href="#">Our Services</a><a href="#">Membership</a><a href="#">Open an Account</a><a href="#">Become a member</a><a href="#">Contact</a>
  </nav>
</header>

<section class="abs banner" role="img" aria-label="Rotating banner photo: delighted trader at a laptop in front of a rising red stock chart">
  <div class="banner-caption">
    <strong>Lorem ipsum dolor sit amet,</strong><span>consectetur adipisicing elit, sed do eiusmod</span>
    <div class="thumbs" role="img" aria-label="Gallery thumbnails"><i></i><i></i><i></i><i></i></div>
  </div>
</section>

<aside>
  <div class="abs panel login">
    <div class="panel-title">MEMBERSHIP LOGIN</div>
    <label>Username</label><div class="field"></div>
    <label>Password</label><div class="field"></div>
    <div class="links"><a href="#">Register</a> &nbsp;|&nbsp; <a href="#">Forgot Password</a></div>
    <span class="btn-login">Login</span>
  </div>

  <div class="abs cta">Register for Daily Market<br>Report / research blog</div>

  <div class="abs panel indices">
    <div class="panel-title">MARKET INDICIES</div>
    <table>
      <tr><th>Name</th><th>Value</th><th>+/-</th><th>%+/-</th></tr>
      <tr><td>Main Ords</td><td>4,511.90</td><td class="dn">-14.70</td><td class="dn">-0.32</td></tr>
      <tr><td>Top200</td><td>4,490.74</td><td class="dn">-14.56</td><td class="dn">-0.32</td></tr>
      <tr><td>Ind30</td><td>13,434.05</td><td class="dn">-39.48</td><td class="dn">-0.29</td></tr>
      <tr><td>HK Idx</td><td>20,919.60</td><td class="dn">-17.68</td><td class="dn">-0.08</td></tr>
      <tr><td>TechComp</td><td>3,066.87</td><td class="up">+1.85</td><td class="up">+0.06</td></tr>
      <tr><td>Tokyo225</td><td>8,596.23</td><td class="dn">-173.36</td><td class="dn">-1.98</td></tr>
      <tr><td>Broad500</td><td>1,441.48</td><td>-</td><td>-</td></tr>
    </table>
  </div>

  <div class="abs panel news">
    <div class="panel-title">BREAKING NEWS</div>
    <ul>
      <li><time>11:43 PM</time><a href="#">Kestrel says India could see rating cut</a></li>
      <li><time>11:43 PM</time><a href="#">Kestrel says India could see rating cut</a></li>
      <li><time>11:43 PM</time><a href="#">Kestrel says India could see rating cut</a></li>
      <li><time>11:43 PM</time><a href="#">Kestrel says India could see rating cut</a></li>
      <li><time>11:43 PM</time><a href="#">Kestrel says India could see rating cut</a></li>
      <li><time>11:43 PM</time><a href="#">Kestrel says India could see rating cut</a></li>
      <li><time>11:43 PM</time><a href="#">Kestrel says India could see rating cut</a></li>
    </ul>
    <div class="news-foot"><b>Vantro</b><span class="more">Read more +</span></div>
  </div>

  <div class="abs panel tweets">
    <div class="panel-title">KV TRADING -<br>MARKET TWEETS</div>
    <div class="tw">IND30 13583 - 26.50(-0.19%), FUT 200 +6 (0.13%) <a href="#">#mkts #ausbiz</a><small>about 8 hours ago</small></div>
    <div class="tw">Switzerland: Unemployment Rate steady at 2.8% in September <a href="#">ratesdesk.com #forex #fx</a><small>about 9 hours ago</small></div>
    <div class="tw">3 Numbers to Watch: US Nonfarm Payrolls, German factory orders &amp; Canadian jobs. <a href="#">http://lnk.to/qRt8m</a><small>about 9 hours ago</small></div>
    <div class="follow-tw"><a href="#">&#8250;&nbsp; Follow us on Chirpline</a></div>
  </div>
</aside>

<main class="abs content">
  <h1>Welcome to KV Trading</h1>
  <p>KV Trading is a full-service brokerage company located on the Gold Coast (Australia). Our company trades Australian stocks, options on Australian stocks, commodities (gold, silver, light oil) and CFD through Marlow trading platform on behalf of our clients.</p>
  <p>Our main advantages are :</p>
  <ol class="adv">
    <li><span class="num">1</span><span><a href="#">Higher potential return.</a> Trading options on Australian stocks or commodities such as gold and silver, you spend much less money and make almost the same profit as if you buy or sell Australian stocks.</span></li>
    <li><span class="num">2</span><span><a href="#">Low Brokerage</a> commission and cost efficiency. Options have great leveraging power. You can obtain an option position that will mimic your stock position almost identically, but at a huge cost savings.</span></li>
    <li><span class="num">3</span><span><a href="#">Comprehensive education.</a> Many investors have avoided options and commodities, believing them to be sophisticated and, therefore, too difficult to understand. Many more have had bad initial experiences with options because neither they nor their brokers were properly trained in how to use them. The improper use of options, like that of any powerful tool, can lead to major problems. If you become a KV Trading Member, we will teach you how to trade options for FREE!!! Furthermore, you will get access to our research and daily reports.</span></li>
  </ol>
  <p>Our main objective is to increase clients' wealth by regularly reviewing their trading portfolio, providing research and education and simplifying their trading through a personalised and professional service.</p>
  <p>We believe that constant communication with our clients' allows for transparency in what we do and ensures a long term relationship built on trust and commitment.</p>
  <p>Whether you are an experienced trader or have just started your portfolio, KV Trading welcomes you with a commitment to profitable trading and superior client/advisor relationships.</p>
  <p>Our unique blend of experience across funds management and technical analysis coupled with enthusiasm and drive for success, creates the perfect climate for you to capitalise on your resources.</p>
  <p>KV Trading offers a full range of products and services from which you can choose:</p>
  <p class="services"><a href="#" style="margin-left:0">KV MEMBERSHIP</a> | <a href="#">BROKERAGE</a> | <a href="#">EDUCATION &amp; MENTORING</a> | <a href="#">RESEARCH</a></p>
  <p>For more information on how you can benefit from being a KV Trading Member, call one of our friendly consultants today on <b>+61 (0) 7 5518 2736</b>, sign up for a free <a href="#">7 DAY TRIAL</a> or contact us via our contact page for a FREE one on one consultation.</p>
  <p>&nbsp;KV Trading (QLD) Pty Ltd holds an Australian Financial Services License (AFSL: 402719)</p>
</main>

<section>
  <div class="abs box active" style="left:112px;top:878px">
    <h2>EDUCATION</h2>
    <p>Lorem ipsum dolor sit amet, consectetur adipisicing elit, sed do eiusmod tempor incididunt ut labore et dolore magna aliqua. Ut enim ad minim veniam...</p>
    <a href="#">Click here for more +</a>
  </div>
  <div class="abs box" style="left:336px;top:878px">
    <h2>MARKET INFORMATION<br>AND RESEARCH</h2>
    <p>Lorem ipsum dolor sit amet, consectetur adipisicing elit, sed do eiusmod tempor incididunt ut labore et dolore magna aliqua. Ut enim ad minim veniam...</p>
    <a href="#">Click here for more +</a>
  </div>
  <div class="abs box" style="left:112px;top:1002px">
    <h2>FULL SERVICE BROKER</h2>
    <p>Lorem ipsum dolor sit amet, consectetur adipisicing elit, sed do eiusmod tempor incididunt ut labore et dolore magna aliqua. Ut enim ad minim veniam...</p>
    <a href="#">Click here for more +</a>
  </div>
  <div class="abs box" style="left:336px;top:1002px">
    <h2>TRADE COMMODITIES<br>AND OPTIONS</h2>
    <p>Lorem ipsum dolor sit amet, consectetur adipisicing elit, sed do eiusmod tempor incididunt ut labore et dolore magna aliqua. Ut enim ad minim veniam...</p>
    <a href="#">Click here for more +</a>
  </div>
</section>

<footer class="abs footer">
  <div><a href="#">Careers</a> &nbsp;/&nbsp; <a href="#">Partners</a> &nbsp;/&nbsp; <a href="#">Legal Privacy FSG</a> &nbsp;/ <a href="#">Site Map</a></div>
  <div style="color:var(--dark);margin-top:3px">© 2012 KV Trading (QLD) Pty Ltd, All Rights Reserved.</div>
  <div class="right">
    <span>
      <svg width="8" height="10" viewBox="0 0 8 10"><rect x="1" y="0.5" width="6" height="9" rx="1" fill="none" stroke="#1685c8"/><rect x="3" y="7" width="2" height="1" fill="#1685c8"/></svg>
      1300 482 917</span>
    <span>|</span>
    <span>
      <svg width="11" height="8" viewBox="0 0 11 8"><rect x="0.5" y="0.5" width="10" height="7" fill="none" stroke="#1685c8"/><path d="M0.5 0.5 5.5 4.5 10.5 0.5" fill="none" stroke="#1685c8"/></svg>
      <a href="#">info@kvtrading.com</a></span>
    <span>|</span>
    <span>Follow on</span><span class="social">Friendwall</span><span class="social">Chirpline</span>
  </div>
</footer>

</body>
</html>
```